"Harbor Builders" is a residential building company and needs a new business card design and may re

We would like a redesign based on the existing logo, and would like to see a new font as well. We are bespoke home builders who build sustainable energy efficient homes.

Industry/Entity Type

Construction

Contact Information for Business Card

Business card size 40mm x 90mm

Colors

Designer to choose colors to be used in the design.

```html
<!DOCTYPE html>
<html lang="en">
<head>
<meta charset="utf-8">
<title>Harbor Builders – Business Card</title>
<link href="https://fonts.googleapis.com/css2?family=Roboto:wght@400;500&family=Roboto+Condensed:wght@700&display=swap" rel="stylesheet">
<style>
  :root {
    --backdrop: #e6e1da;
    --lime: #bdd630;
    --ink: #2b2b2b;
    --text: #4a4a48;
    --block-light: #ffffff;
    --block-shade: #e4e4e2;
    --night: #151617;
    --night-deep: #0b0b0c;
    --night-soft: #1f2021;
    --muted: #3a3b3c;
  }
  * { margin: 0; padding: 0; box-sizing: border-box; }
  html, body { width: 1200px; height: 960px; overflow: hidden; }
  body {
    background: var(--backdrop);
    position: relative;
    font-family: "Roboto", Arial, sans-serif;
  }
  .card {
    position: absolute;
    width: 600px;
    height: 343px;
    overflow: hidden;
    box-shadow: 0 4px 10px rgba(0,0,0,0.25);
  }
  .card--front { left: 302px; top: 129px; background: var(--lime); }
  .card--back { left: 300px; top: 488px; background: var(--night); }

  .feature-block { position: absolute; right: 0; top: 0; width: 372px; height: 343px; }

  .holder-name {
    position: absolute; left: 31px; top: 30px;
    font-family: "Roboto Condensed", Arial, sans-serif;
    font-weight: 700; font-size: 20px; color: var(--ink);
  }
  .wordmark {
    position: absolute; left: 440px; top: 74px;
    font-weight: 500; font-size: 24px; color: var(--ink);
    display: flex; align-items: center; gap: 8px;
  }
  .wordmark__square { width: 14px; height: 14px; background: var(--ink); }

  .company-details {
    position: absolute; left: 31px; top: 158px;
    font-size: 14px; line-height: 19px; color: var(--text);
  }
  .company-details__name { font-weight: 500; }
  .company-details__reg { margin-top: 1px; }
  .contact-list { list-style: none; margin-top: 6px; }
  .contact-list li { display: flex; align-items: center; gap: 8px; height: 19.5px; }
  .contact-list svg { width: 13px; height: 13px; fill: var(--ink); flex: none; }

  .back-wordmark {
    position: absolute; left: 50px; top: 222px;
    font-weight: 500; font-size: 40px; color: var(--night-deep);
  }
  .back-web {
    position: absolute; left: 51px; top: 304px;
    font-size: 14px; color: var(--muted);
  }
</style>
</head>
<body>

<section class="card card--front">
  <svg class="feature-block" viewBox="0 0 372 343" role="img" aria-label="Large white building block decoration">
    <defs>
      <linearGradient id="blockFront" x1="0" y1="0" x2="1" y2="1">
        <stop offset="0" stop-color="#f7f9ee"/>
        <stop offset="0.5" stop-color="#ffffff"/>
        <stop offset="1" stop-color="#e4e4e2"/>
      </linearGradient>
    </defs>
    <polygon points="0,100 268,0 372,0 372,343 230,343 0,250" fill="url(#blockFront)"/>
  </svg>
  <h1 class="holder-name">DANIEL MORROW</h1>
  <div class="wordmark"><span class="wordmark__square"></span>Harbor Builders</div>
  <div class="company-details">
    <p class="company-details__name">Harbor Builders Pty Ltd</p>
    <p>PO Box 7214 Eastgate</p>
    <p>LPO Bayside WA 6091</p>
    <p class="company-details__reg">Registration 48317</p>
    <p>ABN: 42 905 316 774</p>
    <ul class="contact-list">
      <li><svg viewBox="0 0 13 13"><path d="M3.5 0h6a1 1 0 0 1 1 1v11a1 1 0 0 1-1 1h-6a1 1 0 0 1-1-1V1a1 1 0 0 1 1-1zm.5 2v8h5V2zm2.5 8.8a.8.8 0 1 0 0 1.6.8.8 0 0 0 0-1.6z"/></svg>0491 203 587</li>
      <li><svg viewBox="0 0 13 13"><path d="M0 3h13v1L6.5 8 0 4zm0 2.3 6.5 4 6.5-4V11H0z"/></svg>daniel@harborbuilders.com.au</li>
      <li><svg viewBox="0 0 13 13"><circle cx="6.5" cy="6.5" r="6"/><path d="M3 4h3v3H4zM8 7h2.5L9 10z" fill="#bdd630"/></svg>www.harborbuilders.com.au</li>
    </ul>
  </div>
</section>

<section class="card card--back">
  <svg class="feature-block" viewBox="0 0 372 343" role="img" aria-label="Large dark building block decoration">
    <defs>
      <linearGradient id="blockBack" x1="0" y1="0" x2="1" y2="1">
        <stop offset="0" stop-color="#0a0a0b"/>
        <stop offset="0.6" stop-color="#1c1d1e"/>
        <stop offset="1" stop-color="#0b0b0c"/>
      </linearGradient>
    </defs>
    <polygon points="0,100 268,0 372,0 372,343 230,343 0,250" fill="url(#blockBack)"/>
  </svg>
  <p class="back-wordmark">Harbor Builders</p>
  <p class="back-web">www.harborbuilders.com.au</p>
</section>

</body>
</html>
```